Bright Path Notes Wordpress Blog

I need to design a WordPress blog page. The name of the Blog is "Bright Path Notes". I am hoping for a simple design that is easy for me to post future posts to. I like the color teal for this. The website is brightpathnotesblog.com where I am going to write a personal blog. I don't have a logo for this, but am hoping for a header that has some swirly, but classy looking text. Easy on the eyes. The website will only have a couple of pages - the home landing page, and an about me page.

Font styles to use
Script

Colors
00a990
86cfc6
cfeae6

Requirements
Must have
• A header for the landing page of the blog. Clean layout of where the blog posts will lie.

```html
<!DOCTYPE html>
<html lang="en">
<head>
<meta charset="utf-8">
<title>Bright Path Notes</title>
<link href="https://fonts.googleapis.com/css2?family=Raleway:wght@500;600;700;800&family=Open+Sans:ital,wght@0,400;0,600;0,700;1,400&display=swap" rel="stylesheet">
<style>
:root{
  --teal:#0d7f7c;
  --teal-bright:#00a990;
  --teal-soft:#86cfc6;
  --teal-pale:#cfeae6;
  --ink:#1f2a2e;
  --body:#4a4f52;
  --line:#e3e6e6;
  --panel:#f4f5f5;
  --footer:#0b3b3a;
  --navy:#0a1f2c;
  --white:#ffffff;
}
*{box-sizing:border-box;margin:0;padding:0}
html,body{width:1200px;height:3557px;overflow:hidden}
body{position:relative;background:var(--white);font-family:"Open Sans",Arial,sans-serif;color:var(--body)}
.abs{position:absolute}

/* hero */
.hero{left:0;top:0;width:1200px;height:590px;overflow:hidden}
.hero-photo{position:absolute;inset:0;background:
  radial-gradient(circle at 880px 330px,rgba(255,246,220,.95) 0,rgba(240,226,196,.6) 90px,rgba(200,190,170,0) 260px),
  linear-gradient(90deg,#5d6466 0%,#8a8b84 30%,#b4ab98 55%,#a08a72 78%,#6e5a47 90%,#4a3a2d 100%)}
.hero-wave{position:absolute;left:0;top:0}
.topbar{left:161px;top:36px;width:878px;height:34px;display:flex;align-items:center;justify-content:space-between}
.brand{font-family:"Raleway",Arial,sans-serif;font-weight:600;font-size:21px;letter-spacing:.5px;color:var(--white);text-transform:uppercase}
.nav{display:flex;align-items:center;gap:42px;font-family:"Raleway",Arial,sans-serif;font-weight:700;font-size:13px;color:var(--white);text-transform:uppercase}
.nav .active{border-bottom:2px solid var(--white);padding-bottom:4px}
.hero-title{left:161px;top:222px;font-family:"Raleway",Arial,sans-serif;font-weight:700;font-size:47px;line-height:56px;color:var(--white);text-transform:uppercase}
.dots{left:161px;top:462px;display:flex;gap:4px}
.dots span{width:14px;height:14px;border-radius:50%;background:var(--white)}
.dots span.off{background:transparent;border:2px solid var(--white)}

/* section headings */
.section-title{font-family:"Raleway",Arial,sans-serif;font-weight:700;font-size:22px;color:var(--ink)}

/* posts */
.post{left:161px;width:579px;height:272px;border-bottom:1px solid var(--line)}
.post-photo{position:absolute;left:0;top:0;width:268px;height:220px}
.post-body{position:absolute;left:283px;top:0;width:296px}
.post-cat{font-size:11px;font-weight:600;color:var(--ink);text-transform:uppercase;margin-top:10px}
.post-title{font-family:"Raleway",Arial,sans-serif;font-weight:700;font-size:19.5px;line-height:25px;color:var(--teal);margin-top:10px}
.post-text{font-size:11px;line-height:17.5px;color:var(--body);margin-top:9px}
.post-actions{display:flex;align-items:center;gap:6px;margin-top:12px;font-size:10.5px;color:var(--ink)}
.btn-ghost{border:1px solid #cfd3d3;height:23px;padding:0 11px;display:flex;align-items:center}
.btn-icon{border:1px solid #cfd3d3;width:27px;height:23px;display:flex;align-items:center;justify-content:center}
.share{display:flex;align-items:center;gap:5px;margin-left:4px}
.share i{width:6px;height:6px;background:var(--ink);border-radius:1px;display:block}

/* about section */
.goals-head{left:161px;top:2556px}
.goals-sub{left:161px;top:2598px;width:579px;font-family:"Raleway",Arial,sans-serif;font-weight:700;font-size:17.5px;color:var(--teal)}
.goals-text{left:161px;top:2632px;width:579px;font-size:11px;line-height:17.5px}
.tile{position:absolute}

.pager{left:161px;top:3243px;display:flex;border:1px solid var(--line)}
.pager span{width:27px;height:42px;display:flex;align-items:center;justify-content:center;font-size:10px;color:var(--ink);border-right:1px solid var(--line)}
.pager span.current{background:#000;color:var(--white);width:54px}
.pager span.next{width:56px;border-right:0;font-weight:700}

/* sidebar */
.search{left:783px;top:667px;width:256px;height:36px;border:1px solid var(--teal);display:flex;align-items:center;justify-content:space-between;padding:0 12px;font-size:11px;color:var(--ink)}
.panel{left:783px;width:256px;background:var(--panel);border:1px solid var(--line);padding:19px 19px 0}
.panel-photo{width:218px}
.panel-title{font-family:"Raleway",Arial,sans-serif;font-weight:700;font-size:19px;color:var(--ink)}
.panel-text{font-size:11px;line-height:17.5px}
.btn-teal{display:inline-block;background:var(--teal);color:var(--white);font-size:10px;font-weight:700;padding:7px 12px;text-transform:uppercase}
.recent-title{font-family:"Raleway",Arial,sans-serif;font-weight:700;font-size:15px;color:var(--teal)}
.meta{font-size:10.5px;font-style:italic;font-weight:600;color:var(--ink);display:flex;align-items:center;gap:6px}
.arrows{display:flex;gap:6px}
.arrows span{width:19px;height:19px;border:1px solid #8a8f90;border-radius:50%;display:flex;align-items:center;justify-content:center}

.subscribe{left:783px;top:1644px;width:256px;height:254px;background:var(--teal);padding:32px 17px 0;color:var(--white)}
.subscribe h3{font-family:"Raleway",Arial,sans-serif;font-weight:700;font-size:19px;text-align:left}
.subscribe p{font-size:11px;line-height:16px;margin-top:10px}
.field{background:var(--white);height:36px;margin-top:9px;font-size:10.5px;color:var(--ink);display:flex;align-items:center;padding:0 10px}
.field.first{margin-top:13px}
.btn-navy{background:var(--navy);height:36px;margin-top:14px;display:flex;align-items:center;justify-content:center;font-weight:700;font-size:15px;color:var(--white)}

.top-item{border-top:1px solid var(--line);padding:16px 0 14px}
.top-item:first-of-type{border-top:0}

/* footer */
.footer{left:0;top:3356px;width:1200px;height:201px;background:var(--footer);color:var(--white)}
.social{position:absolute;top:36px;left:0;width:1200px;display:flex;justify-content:center;gap:12px}
.social span{width:40px;height:40px;border:2px solid var(--white);border-radius:50%;display:flex;align-items:center;justify-content:center}
.social span i{width:10px;height:10px;background:var(--white);border-radius:50%;display:block}
.foot-nav{position:absolute;top:110px;left:0;width:1200px;display:flex;justify-content:center;gap:22px;font-size:11.5px;font-weight:600;text-transform:uppercase}
.foot-copy{position:absolute;top:144px;left:0;width:1200px;text-align:center;font-size:10.5px;color:#cfe3e1}
</style>
</head>
<body>

<header class="abs hero">
  <div class="hero-photo" role="img" aria-label="Climber scaling a tall rock face against a hazy sunlit sky"></div>
  <svg class="hero-wave" width="1200" height="590" viewBox="0 0 1200 590">
    <path d="M0 505 C 250 545, 420 575, 620 560 C 820 545, 1000 470, 1200 455 L1200 590 L0 590 Z" fill="#0d7f7c"/>
    <path d="M0 540 C 260 575, 430 600, 640 588 C 840 575, 1010 505, 1200 485 L1200 590 L0 590 Z" fill="#0a6462" opacity=".6"/>
    <path d="M0 552 C 260 588, 440 615, 650 600 C 850 585, 1020 525, 1200 505 L1200 590 L0 590 Z" fill="#ffffff"/>
  </svg>
  <div class="abs topbar">
    <div class="brand">Bright Path Notes</div>
    <nav class="nav">
      <span class="active">Home</span>
      <span>About Mara</span>
      <span>Contact</span>
      <svg width="16" height="16" viewBox="0 0 16 16"><circle cx="6.5" cy="6.5" r="5" fill="none" stroke="#fff" stroke-width="2"/><line x1="10.3" y1="10.3" x2="15" y2="15" stroke="#fff" stroke-width="2.4"/></svg>
    </nav>
  </div>
  <h1 class="abs hero-title">Bright Path<br>Notes</h1>
  <div class="abs dots"><span class="off"></span><span></span><span></span></div>
</header>

<h2 class="abs section-title" style="left:161px;top:594px">Latest Blog News</h2>

<main>
  <article class="abs post" style="top:650px">
    <div class="post-photo" role="img" aria-label="Person standing at the top of a long staircase toward bright light" style="background:linear-gradient(180deg,#eef1f1,#9aa3a4 55%,#2d3436)"></div>
    <div class="post-body">
      <div class="post-cat">Categories // Growth, Goals, Loremis</div>
      <h3 class="post-title">At vero eos et accu losamusiuo odio dignissimos ducimus</h3>
      <p class="post-text">Lorem ipsum dolor sit amet, consectetur adipiscing elit, sdo eiusmod tempor incididunt ut labore et dolo re magna alut enimadminim veniam, quis nostrud exercitation ullamcabo ris nisi ut aliq lorulp ex commocon sequatus.</p>
      <div class="post-actions"><span class="btn-ghost">View More</span><span class="btn-icon">▢</span><span class="btn-icon">▤</span><span class="share">&lt; Share This <i></i><i></i><i></i><i></i></span></div>
    </div>
  </article>

  <article class="abs post" style="top:920px">
    <div class="post-photo" role="img" aria-label="Man in a suit with arms spread wide against a warm sky" style="background:linear-gradient(135deg,#f3c98a,#c98a52 50%,#6b4a3a)"></div>
    <div class="post-body">
      <div class="post-cat">Categories // Growth, Goals, Loremis</div>
      <h3 class="post-title">At vero eos et accu losamusiuo odio dignissimos ducimus</h3>
      <p class="post-text">Lorem ipsum dolor sit amet, consectetur adipiscing elit, sdo eiusmod tempor incididunt ut labore et dolo re magna alut enimadminim veniam, quis nostrud exercitation ullamcabo ris nisi ut aliq lorulp ex commocon sequatus.</p>
      <div class="post-actions"><span class="btn-ghost">View More</span><span class="btn-icon">▢</span><span class="btn-icon">▤</span><span class="share">&lt; Share This <i></i><i></i><i></i><i></i></span></div>
    </div>
  </article>

  <article class="abs post" style="top:1190px">
    <div class="post-photo" role="img" aria-label="Person raising arms toward a golden sunset over the sea" style="background:linear-gradient(180deg,#f6e3a6,#e9b24e 55%,#8b6a3a)"></div>
    <div class="post-body">
      <div class="post-cat">Categories // Growth, Goals, Loremis</div>
      <h3 class="post-title">At vero eos et accu losamusiuo odio dignissimos ducimus</h3>
      <p class="post-text">Lorem ipsum dolor sit amet, consectetur adipiscing elit, sdo eiusmod tempor incididunt ut labore et dolo re magna alut enimadminim veniam, quis nostrud exercitation ullamcabo ris nisi ut aliq lorulp ex commocon sequatus.</p>
      <div class="post-actions"><span class="btn-ghost">View More</span><span class="btn-icon">▢</span><span class="btn-icon">▤</span><span class="share">&lt; Share This <i></i><i></i><i></i><i></i></span></div>
    </div>
  </article>

  <article class="abs post" style="top:1461px">
    <div class="post-photo" role="img" aria-label="Hand drawing a bow and arrow toward a target" style="background:linear-gradient(90deg,#e6e2dc,#c9a98b 55%,#5a4232)"></div>
    <div class="post-body">
      <div class="post-cat">Categories // Growth, Goals, Loremis</div>
      <h3 class="post-title">At vero eos et accu losamusiuo odio dignissimos ducimus</h3>
      <p class="post-text">Lorem ipsum dolor sit amet, consectetur adipiscing elit, sdo eiusmod tempor incididunt ut labore et dolo re magna alut enimadminim veniam, quis nostrud exercitation ullamcabo ris nisi ut aliq lorulp ex commocon sequatus.</p>
      <div class="post-actions"><span class="btn-ghost">View More</span><span class="btn-icon">▢</span><span class="btn-icon">▤</span><span class="share">&lt; Share This <i></i><i></i><i></i><i></i></span></div>
    </div>
  </article>

  <article class="abs post" style="top:1731px">
    <div class="post-photo" role="img" aria-label="Hiker standing on a rocky mountain ridge above valleys" style="background:linear-gradient(180deg,#cfe0ea,#9fb3bd 50%,#5c5a52)"></div>
    <div class="post-body">
      <div class="post-cat">Categories // Growth, Goals, Loremis</div>
      <h3 class="post-title">At vero eos et accu losamusiuo odio dignissimos ducimus</h3>
      <p class="post-text">Lorem ipsum dolor sit amet, consectetur adipiscing elit, sdo eiusmod tempor incididunt ut labore et dolo re magna alut enimadminim veniam, quis nostrud exercitation ullamcabo ris nisi ut aliq lorulp ex commocon sequatus.</p>
      <div class="post-actions"><span class="btn-ghost">View More</span><span class="btn-icon">▢</span><span class="btn-icon">▤</span><span class="share">&lt; Share This <i></i><i></i><i></i><i></i></span></div>
    </div>
  </article>

  <article class="abs post" style="top:2004px">
    <div class="post-photo" role="img" aria-label="Runner crouched at a start line on a city road at sunrise" style="background:linear-gradient(180deg,#d9c48f,#8c7c56 50%,#3a3731)"></div>
    <div class="post-body">
      <div class="post-cat">Categories // Growth, Goals, Loremis</div>
      <h3 class="post-title">At vero eos et accu losamusiuo odio dignissimos ducimus</h3>
      <p class="post-text">Lorem ipsum dolor sit amet, consectetur adipiscing elit, sdo eiusmod tempor incididunt ut labore et dolo re magna alut enimadminim veniam, quis nostrud exercitation ullamcabo ris nisi ut aliq lorulp ex commocon sequatus.</p>
      <div class="post-actions"><span class="btn-ghost">View More</span><span class="btn-icon">▢</span><span class="btn-icon">▤</span><span class="share">&lt; Share This <i></i><i></i><i></i><i></i></span></div>
    </div>
  </article>

  <article class="abs post" style="top:2277px">
    <div class="post-photo" role="img" aria-label="Wooden figures on a board with one raised above the rest" style="background:linear-gradient(135deg,#a2583f,#7a3c2c 60%,#4d261d)"></div>
    <div class="post-body">
      <div class="post-cat">Categories // Growth, Goals, Loremis</div>
      <h3 class="post-title">At vero eos et accu losamusiuo odio dignissimos ducimus</h3>
      <p class="post-text">Lorem ipsum dolor sit amet, consectetur adipiscing elit, sdo eiusmod tempor incididunt ut labore et dolo re magna alut enimadminim veniam, quis nostrud exercitation ullamcabo ris nisi ut aliq lorulp ex commocon sequatus.</p>
      <div class="post-actions"><span class="btn-ghost">View More</span><span class="btn-icon">▢</span><span class="btn-icon">▤</span><span class="share">&lt; Share This <i></i><i></i><i></i><i></i></span></div>
    </div>
  </article>

  <section>
    <h2 class="abs section-title goals-head">Bright Path Notes</h2>
    <h3 class="abs goals-sub">Sed ut perspiciatis unde omnis iste naticiatis unde omnis iste.</h3>
    <p class="abs goals-text">Lorem ipsum dolor sit amet, consectetur adipiscing elit, seddo eiusmod tempor incididunt ut labore et dolo re magna aliqut enimadminim veniam, quis nostrud exercitation ullamco laboris nisi ut aliq lorulp ex commocon sequa lotuborem ipsum dolor sit amet, consectetur adipiscing elit, seddo eiusmod tempor incididunt.</p>
    <div class="tile" role="img" aria-label="Hand pointing along a rising line chart" style="left:161px;top:2716px;width:273px;height:311px;background:linear-gradient(135deg,#f1f1f1,#c9c9c9)"></div>
    <div class="tile" role="img" aria-label="Arrows hitting a target board" style="left:444px;top:2716px;width:142px;height:151px;background:linear-gradient(180deg,#c6d0d2,#6f8488)"></div>
    <div class="tile" role="img" aria-label="Hiker celebrating on a snowy summit" style="left:595px;top:2716px;width:143px;height:151px;background:linear-gradient(180deg,#5b87b6,#cfd9e2 60%,#6d6a62)"></div>
    <div class="tile" role="img" aria-label="Hand reaching over a mountain edge above valleys" style="left:444px;top:2877px;width:294px;height:150px;background:linear-gradient(180deg,#b9c7d2,#a28a6f 60%,#5a4a3c)"></div>
    <div class="tile" role="img" aria-label="Climber silhouetted on a peak against a blue sky" style="left:161px;top:3036px;width:273px;height:171px;background:linear-gradient(180deg,#2f6fb4,#a8c6e2 55%,#3b3f45)"></div>
    <div class="tile" role="img" aria-label="Two hands joining puzzle pieces against a sunset" style="left:444px;top:3036px;width:294px;height:171px;background:linear-gradient(180deg,#e39a4f,#b9572c 55%,#3d2a22)"></div>
    <div class="abs pager"><span>1</span><span class="current">2</span><span>3</span><span>4</span><span class="next">NEXT</span></div>
  </section>
</main>

<aside>
  <div class="abs search"><span>Search</span>
    <svg width="12" height="12" viewBox="0 0 16 16"><circle cx="6.5" cy="6.5" r="5" fill="none" stroke="#0d7f7c" stroke-width="2.2"/><line x1="10.3" y1="10.3" x2="15" y2="15" stroke="#0d7f7c" stroke-width="2.6"/></svg>
  </div>

  <div class="abs panel" style="top:733px;height:410px">
    <div class="panel-photo" role="img" aria-label="Portrait of the blog author" style="height:195px;background:linear-gradient(135deg,#e8a24c,#b8672c 60%,#6b3a20)"></div>
    <h3 class="panel-title" style="margin-top:20px">About Us</h3>
    <p class="panel-text" style="margin-top:8px">Lorem ipsum dolor sit amet, consectetur adipiscing elit, sed do eiusmod tempor incid idunt ut labore et dolore magna aliqut enim dminim veniam, quis nostrud.</p>
    <span class="btn-teal" style="margin-top:12px">Read More</span>
  </div>

  <div class="abs panel" style="top:1160px;height:467px">
    <h3 class="panel-title">Recent Posts</h3>
    <div class="panel-photo" role="img" aria-label="Hiker with raised arms on a mountain above the clouds" style="height:152px;margin-top:14px;background:linear-gradient(180deg,#4d7fb6,#c9d6e2 55%,#6b6158)"></div>
    <h4 class="recent-title" style="margin-top:22px">Sed ut perspiciatis uomnis</h4>
    <p class="panel-text" style="margin-top:10px">Lorem ipsum dolor sit amet, consectetur adipiscing elit, sed do eiusmod tempor incid idunt ut labore et dolore magna aliqut.orem ipsum dolor sit amet, consectetur adipiscing elit, sed do eiusmod tempor incididunt ut labore et dolore magna aliqut.</p>
    <div class="meta" style="margin-top:12px">▦ Mar 04, 2017</div>
    <div class="arrows" style="margin-top:20px"><span><svg width="8" height="8" viewBox="0 0 8 8"><path d="M5.5 1 L2.5 4 L5.5 7" fill="none" stroke="#555" stroke-width="1.4"/></svg></span><span><svg width="8" height="8" viewBox="0 0 8 8"><path d="M2.5 1 L5.5 4 L2.5 7" fill="none" stroke="#555" stroke-width="1.4"/></svg></span></div>
  </div>

  <div class="abs subscribe">
    <h3>Subscribe to our Blog</h3>
    <p>Lorem ipsum dolor sit amet, consectetulip iscing elit, sed do eiusmod tempo.</p>
    <div class="field first">Name:</div>
    <div class="field">Email:</div>
    <div class="btn-navy">Subscribe</div>
  </div>

  <div class="abs panel" style="top:1917px;height:536px">
    <div class="panel-photo" role="img" aria-label="Person facing a large target on a wall" style="height:259px;background:radial-gradient(circle at 50% 40%,#f4f4f4,#c3c7c9 45%,#5d6569)"></div>
    <h3 class="panel-title" style="margin-top:28px">Top Posts</h3>
    <div class="top-item"><h4 class="recent-title">Sopiciatis unde &nbsp;voluptatem</h4><p class="panel-text" style="margin-top:4px">Lorem ipsum dolor sit amet, cons lorectetur adipiscing elit, sed do eiusmod temp</p></div>
    <div class="top-item"><h4 class="recent-title">Sopiciatis unde &nbsp;voluptatem</h4><p class="panel-text" style="margin-top:4px">Lorem ipsum dolor sit amet, cons lorectetur adipiscing elit, sed do eiusmod temp</p></div>
    <div class="top-item"><h4 class="recent-title">Sopiciatis unde &nbsp;voluptatem</h4><p class="panel-text" style="margin-top:4px">Lorem ipsum dolor sit amet, cons lorectetur adipiscing elit, sed do eiusmod temp</p></div>
  </div>
</aside>

<footer class="abs footer">
  <div class="social"><span><i></i></span><span><i></i></span><span><i></i></span><span><i></i></span><span><i></i></span></div>
  <nav class="foot-nav"><span>Home</span><span>//</span><span>About Mara</span><span>//</span><span>Contact</span><span>//</span><span>Our News</span><span>//</span><span>Sitemap</span></nav>
  <p class="foot-copy">© 2017 All copyrights reserved.Bright Path Notes. Privacy Policy And Terms And Conditions</p>
</footer>

</body>
</html>
```